The Copperline Collective's website for high impact furniture promotions

I am looking for a simple website. we are a promotional company that runs events for furniture stores to increase sales for short periods of time. i would like the website to have about 4 areas to explain our company. I would like it to be simple and user friendly. I would like a link to chatterbook and a contact section. I am attaching our logo that i would like somewhere large or possibly in the backround. I am open to different color schemes. I would like to convey fast paced, modern, reliable. I am open to all different styles and look forward to seeing whats out there. we are looking for a quick turn around, so if we see one that we like quick, we will pick that one thanks
Reason: looking for some really creative designs and want to give a fair amount of time to produce
Target Market(s)
Retail Furniture store owners
Industry/Entity Type
It Company
Number of Pages Required
1 page
Colors
Designer to choose colors to be used in the design.
Look and feel

```html
<!DOCTYPE html>
<html lang="en">
<head>
<meta charset="utf-8">
<title>The Copperline Collective</title>
<link href="https://fonts.googleapis.com/css2?family=Montserrat:wght@400;600;700&family=Open+Sans:wght@400;600;700&display=swap" rel="stylesheet">
<style>
:root{
  --red:#e8343c;
  --red-dark:#c8232b;
  --ink:#222;
  --muted:#555;
  --grey-bg:#ebebeb;
  --footer:#1b1d22;
  --footer-text:#c9c9c9;
  --white:#fff;
  --copper:#a9773f;
}
*{box-sizing:border-box;margin:0;padding:0}
html,body{width:1200px;height:3232px;overflow:hidden}
body{position:relative;font-family:"Open Sans",Arial,sans-serif;color:var(--ink);background:var(--white)}
.abs{position:absolute}
h2.section-title{position:absolute;left:0;width:1200px;text-align:center;font-family:"Montserrat",Arial,sans-serif;font-weight:700;font-size:28px;color:var(--red);letter-spacing:.5px}
.rule{position:absolute;left:540px;width:120px;height:2px;background:var(--red)}

/* nav */
.topbar{position:absolute;left:0;top:0;width:1200px;height:82px;background:var(--white);border-top:3px solid #1c2a5a;z-index:3}
.nav a{position:absolute;top:30px;font-family:"Montserrat",Arial,sans-serif;font-size:17px;color:var(--ink);text-decoration:none;font-weight:400}
.brand-tab{position:absolute;left:480px;top:-40px;width:240px;height:240px;border-radius:50%;background:var(--white);z-index:4;text-align:center}
.brand-tab .name{margin-top:92px;font-family:"Open Sans",Arial,sans-serif;font-weight:600;font-size:20px;line-height:1.25;color:var(--copper)}

/* hero */
.hero{position:absolute;left:0;top:0;width:1200px;height:625px;background:linear-gradient(180deg,#3c4a4f 0%,#52605f 45%,#6d7472 70%,#8e9290 100%)}
.hero-photo{position:absolute;left:0;top:0;width:1200px;height:625px}
.hero-shade{position:absolute;left:0;top:0;width:1200px;height:625px;background:rgba(0,0,0,.25)}
.hero h1{position:absolute;top:236px;left:0;width:1200px;text-align:center;font-family:"Montserrat",Arial,sans-serif;font-weight:700;font-size:50px;color:var(--white)}
.hero p{position:absolute;top:322px;left:250px;width:700px;text-align:center;font-weight:600;font-size:19px;line-height:30px;color:var(--white)}
.btn-more{position:absolute;left:534px;top:416px;width:132px;height:50px;background:var(--red);border:2px solid var(--white);color:var(--white);font-family:"Montserrat",Arial,sans-serif;font-size:16px;line-height:46px;text-align:center}
.dots{position:absolute;top:575px;left:546px;display:flex;gap:6px}
.dots span{width:17px;height:17px;border-radius:50%;background:#cfcfcf}
.dots span.on{background:var(--red);border:2px solid var(--white)}

/* why */
.why-intro{position:absolute;top:800px;left:118px;width:964px;text-align:center;font-size:14px;line-height:26px;color:var(--muted)}
.card{position:absolute;top:896px;width:282px;height:280px;background:var(--white);box-shadow:0 1px 6px rgba(0,0,0,.18);text-align:center}
.card svg{margin-top:36px}
.card h3{margin-top:18px;font-family:"Montserrat",Arial,sans-serif;font-weight:700;font-size:18px;color:var(--red)}
.card p{margin:16px 32px 0;font-size:13px;line-height:22px;color:var(--muted)}
.card.active{background:var(--red)}
.card.active h3,.card.active p{color:var(--white)}

/* trading */
.trading{position:absolute;left:0;top:1238px;width:1200px;height:604px}
.trading h2.section-title{top:118px;color:var(--white)}
.trading .rule{top:172px;background:var(--white)}
.trading-lead{position:absolute;top:214px;left:120px;width:960px;text-align:center;font-size:16px;line-height:30px;color:#fde3e4}
.trading-box{position:absolute;top:313px;left:97px;width:1004px;height:161px;background:rgba(255,255,255,.16);padding:38px 30px;text-align:center;font-size:14px;line-height:29px;color:var(--white)}

/* about */
.about-photo{position:absolute;left:97px;top:1895px;width:333px;height:345px}
.about h2{position:absolute;left:504px;top:1888px;font-family:"Montserrat",Arial,sans-serif;font-weight:700;font-size:28px;color:var(--red)}
.about-lead{position:absolute;left:504px;top:1954px;width:600px;font-size:14px;line-height:24px;color:var(--muted)}
.ticks{position:absolute;left:504px;top:2018px;list-style:none}
.ticks li{height:36px;display:flex;align-items:center;gap:12px;font-size:15px;font-weight:600;color:var(--ink)}

/* faq */
.faq{position:absolute;left:0;top:2296px;width:1200px;height:435px;background:var(--grey-bg)}
.faq h2.section-title{top:54px}
.faq .rule{top:100px}
.q{position:absolute;left:101px;width:472px;height:48px;border:2px solid var(--red);border-radius:24px;padding:0 20px;display:flex;align-items:center;justify-content:space-between;font-size:15px;font-weight:600;color:var(--red);background:var(--white)}
.q.open{background:var(--red);color:var(--white)}
.answers{position:absolute;left:622px;top:158px;width:480px}
.answers h4{font-family:"Montserrat",Arial,sans-serif;font-size:21px;font-weight:600;color:var(--red);margin-bottom:14px}
.answers li{list-style:none;display:flex;align-items:center;gap:10px;font-size:15px;color:var(--red);height:30px}
.answers p{margin-top:14px;font-size:13px;line-height:26px;color:var(--muted)}

/* footer */
.footer{position:absolute;left:0;top:2731px;width:1200px;height:501px;background:var(--footer);color:var(--footer-text)}
.foot-brand{position:absolute;left:87px;top:220px;width:200px;text-align:center}
.foot-brand .name{font-weight:600;font-size:20px;line-height:1.25;color:var(--copper)}
.foot-col h5{font-family:"Montserrat",Arial,sans-serif;font-weight:600;font-size:17px;color:var(--white)}
.foot-col .bar{width:84px;height:2px;background:var(--white);margin-top:10px}
.links{list-style:none;margin-top:18px}
.links li{height:32px;font-size:14px;color:var(--white)}
.contact-row{position:absolute;left:0;display:flex;gap:18px}
.ci{width:40px;height:40px;border:2px solid var(--white);border-radius:50%;display:flex;align-items:center;justify-content:center;flex:none}
.contact-row strong{display:block;font-size:15px;color:var(--white);font-weight:700}
.contact-row span{font-size:13px;line-height:22px}
.field{position:absolute;border:1px solid #aaa;border-radius:3px;font-size:11px;color:var(--white);padding:8px 10px}
.send{position:absolute;left:0;width:118px;height:39px;background:var(--red);border:1px solid var(--white);color:var(--white);font-size:12px;line-height:37px;text-align:center}
.foot-rule{position:absolute;left:97px;top:414px;width:1006px;height:1px;background:#555}
.copyright{position:absolute;left:97px;top:446px;font-size:14px;font-weight:600;color:var(--white)}
.social{position:absolute;left:1068px;top:436px;width:34px;height:34px;border:2px solid var(--white);border-radius:50%;color:var(--white);font-size:0}
.social::after{content:"";position:absolute;left:12px;top:9px;width:6px;height:12px;border-radius:2px;background:var(--white)}
</style>
</head>
<body>

<section class="hero">
  <div class="hero-photo" role="img" aria-label="Furniture showroom with a teal sofa against a striped wall"></div>
  <div class="hero-shade"></div>
  <h1>COPPERLINE COLLECTIVE</h1>
  <p>We are a promotional company that runs events for furniture stores to increase sales for short periods of time.</p>
  <div class="btn-more">READ MORE</div>
  <div class="dots"><span class="on"></span><span></span><span></span><span></span><span></span></div>
  <svg class="abs" style="left:0;top:540px" width="1200" height="86" viewBox="0 0 1200 86"><polygon points="0,30 600,86 1200,30 1200,86 0,86" fill="#fff"/></svg>
</section>

<header class="topbar">
  <nav class="nav">
    <a style="left:97px">HOME</a>
    <a style="left:222px">ABOUT US</a>
    <a style="left:378px">TRADING</a>
    <a style="left:750px">STORES</a>
    <a style="left:870px">FURNITURE</a>
    <a style="left:1022px">CONTACT</a>
  </nav>
</header>
<div class="brand-tab"><div class="name">The Copperline<br>Collective</div></div>

<section class="why">
  <h2 class="section-title" style="top:692px">WHY COPPERLINE COLLECTIVE</h2>
  <div class="rule" style="top:755px"></div>
  <p class="why-intro">Duis aute irure dolor in reprehenderit in voluptate velit esse cillum dolore eu fugiat nulla pariatur. Excepteur sint occaecat cupidatat non proident, sunt in culpa qui officiar.</p>

  <div class="card" style="left:123px">
    <svg width="80" height="70" viewBox="0 0 80 70"><path d="M14 28h10l30-16v46L24 42H14z" fill="#e8343c"/><rect x="20" y="42" width="10" height="18" fill="#e8343c"/><path d="M62 26l10-6M64 35h12M62 44l10 6" stroke="#e8343c" stroke-width="4"/></svg>
    <h3>Promotional Company</h3>
    <p>Nemo enim ipsam voluptatem quia voluptas sit aspernatur aut odit aut fugit, sed quia consequuntur.</p>
  </div>
  <div class="card active" style="left:459px">
    <svg width="80" height="70" viewBox="0 0 80 70"><rect x="16" y="6" width="58" height="40" fill="none" stroke="#fff" stroke-width="4"/><path d="M26 36l12-12 8 8 16-16" fill="none" stroke="#fff" stroke-width="4"/><path d="M6 46l14-8 10 10-10 16H6z" fill="#fff"/></svg>
    <h3>Trading Services</h3>
    <p>Nemo enim ipsam voluptatem quia voluptas sit aspernatur aut odit aut fugit, sed quia consequuntur.</p>
  </div>
  <div class="card" style="left:795px">
    <svg width="80" height="70" viewBox="0 0 80 70"><rect x="26" y="4" width="28" height="28" rx="4" fill="#e8343c"/><rect x="20" y="32" width="40" height="10" rx="3" fill="#e8343c"/><rect x="12" y="22" width="8" height="18" fill="#e8343c"/><rect x="60" y="22" width="8" height="18" fill="#e8343c"/><path d="M40 42v14M24 62l16-6 16 6" stroke="#e8343c" stroke-width="4" fill="none"/></svg>
    <h3>Furniture Stores</h3>
    <p>Nemo enim ipsam voluptatem quia voluptas sit aspernatur aut odit aut fugit, sed quia consequuntur.</p>
  </div>
</section>

<section class="trading">
  <svg class="abs" style="left:0;top:0" width="1200" height="604" viewBox="0 0 1200 604" role="img" aria-label="Red-toned living room interior">
    <defs><linearGradient id="tradeFill" x1="0" y1="0" x2="1" y2="1"><stop offset="0" stop-color="#d8262e"/><stop offset=".5" stop-color="#c41f27"/><stop offset="1" stop-color="#b51c24"/></linearGradient></defs>
    <polygon points="0,0 600,50 1200,0 1200,604 600,550 0,604" fill="url(#tradeFill)"/>
  </svg>
  <h2 class="section-title">OUR TRADING</h2>
  <div class="rule"></div>
  <p class="trading-lead">Nemo enim ipsam voluptatem quia voluptas sit aspernatur aut odit aut fugit, sed quia consequuntur magni dolores eos qui ratione voluptatem sequi nesciunt.</p>
  <div class="trading-box">Sed ut perspiciatis unde omnis iste natus error sit voluptatem accusantium doloremque laudantium, totam rem aperiam, eaque ipsa quae ab illo inventore veritatis et quasi architecto beatae vitae dicta sunt explicabo. Nemo enim ipsam voluptatem quia voluptas sit aspernatur aut odit aut fugit, sed quia consequuntur magni dolores eos qui ratione voluptatem.</div>
</section>

<section class="about">
  <div class="about-photo" role="img" aria-label="Brown upholstered armchair with wooden legs" style="background:linear-gradient(180deg,#f4f1ee 0%,#5a4536 25%,#4a382b 60%,#7a4a32 85%,#f2efec 100%)"></div>
  <h2>ABOUT US</h2>
  <p class="about-lead">Nemo enim ipsam voluptatem quia voluptas sit aspernatur aut odit aut fugit, sed quia conse quuntur magni dolores eos qui ratione voluptatem</p>
  <ul class="ticks">
    <li><svg width="20" height="20" viewBox="0 0 20 20"><rect x="1" y="3" width="15" height="15" fill="none" stroke="#e8343c" stroke-width="2"/><path d="M5 10l4 4 9-11" fill="none" stroke="#e8343c" stroke-width="3"/></svg>Nemo enim ipsam voluptatem quia voluptas</li>
    <li><svg width="20" height="20" viewBox="0 0 20 20"><rect x="1" y="3" width="15" height="15" fill="none" stroke="#e8343c" stroke-width="2"/><path d="M5 10l4 4 9-11" fill="none" stroke="#e8343c" stroke-width="3"/></svg>Aspernatur aut odit aut fugit, sed quia consequuntur</li>
    <li><svg width="20" height="20" viewBox="0 0 20 20"><rect x="1" y="3" width="15" height="15" fill="none" stroke="#e8343c" stroke-width="2"/><path d="M5 10l4 4 9-11" fill="none" stroke="#e8343c" stroke-width="3"/></svg>Neque porro quisquam est, qui dolorem ipsum quia dolor sit amet</li>
    <li><svg width="20" height="20" viewBox="0 0 20 20"><rect x="1" y="3" width="15" height="15" fill="none" stroke="#e8343c" stroke-width="2"/><path d="M5 10l4 4 9-11" fill="none" stroke="#e8343c" stroke-width="3"/></svg>Adipisci velit, sed quia non numquam eius modi tempora</li>
    <li><svg width="20" height="20" viewBox="0 0 20 20"><rect x="1" y="3" width="15" height="15" fill="none" stroke="#e8343c" stroke-width="2"/><path d="M5 10l4 4 9-11" fill="none" stroke="#e8343c" stroke-width="3"/></svg>Enim ad minima veniam, quis nostrum exercitationem ullam</li>
    <li><svg width="20" height="20" viewBox="0 0 20 20"><rect x="1" y="3" width="15" height="15" fill="none" stroke="#e8343c" stroke-width="2"/><path d="M5 10l4 4 9-11" fill="none" stroke="#e8343c" stroke-width="3"/></svg>Quis autem vel eum iure reprehenderit qui in ea voluptate</li>
  </ul>
</section>

<section class="faq">
  <h2 class="section-title">OUR FAQ'S</h2>
  <div class="rule"></div>
  <div class="q open" style="top:150px">Nemo enim ipsam voluptatem quia?<span>&#8964;</span></div>
  <div class="q" style="top:212px">Dolores eos qui ratione voluptatem sequi?<span>&raquo;</span></div>
  <div class="q" style="top:274px">Architecto beatae vitae dicta sunt explicabo?<span>&raquo;</span></div>
  <div class="q" style="top:336px">Perspiciatis unde omnis iste natus error sit?<span>&raquo;</span></div>
  <div class="answers">
    <h4>Answers to your questions:</h4>
    <ul>
      <li><svg width="14" height="14"><circle cx="7" cy="7" r="6" fill="#e8343c"/><path d="M5 4l3 3-3 3" stroke="#fff" stroke-width="1.6" fill="none"/></svg>Nemo enim ipsam voluptatem quia voluptas</li>
      <li><svg width="14" height="14"><circle cx="7" cy="7" r="6" fill="#e8343c"/><path d="M5 4l3 3-3 3" stroke="#fff" stroke-width="1.6" fill="none"/></svg>Sed quia non numquam eius modi tempora incidunt</li>
    </ul>
    <p>Sed ut perspiciatis unde omnis iste natus error sit voluptatem accusantium do loremque laudantium, totam rem aperiam.</p>
  </div>
</section>

<footer class="footer">
  <svg class="abs" style="left:0;top:0" width="1200" height="48" viewBox="0 0 1200 48"><polygon points="0,0 1200,0 600,46" fill="#ebebeb"/></svg>
  <div class="foot-brand"><div class="name">The Copperline<br>Collective</div></div>

  <div class="foot-col abs" style="left:340px;top:128px">
    <h5>QUICK LINKS</h5><div class="bar"></div>
    <ul class="links">
      <li>&rsaquo; Home</li><li>&rsaquo; About Us</li><li>&rsaquo; Trading</li><li>&rsaquo; Stores</li><li>&rsaquo; Furniture</li><li>&rsaquo; Contact Us</li>
    </ul>
  </div>

  <div class="foot-col abs" style="left:523px;top:128px;width:260px;height:260px">
    <h5>CONTACT US</h5><div class="bar"></div>
    <div class="contact-row" style="top:60px"><div class="ci"><svg width="14" height="18" viewBox="0 0 14 18"><path d="M7 17C2 10 1 8 1 6a6 6 0 0 1 12 0c0 2-1 4-6 11z" fill="#fff"/><circle cx="7" cy="6" r="2" fill="#1b1d22"/></svg></div><div><strong>ADDRESS,</strong><span>Office 1408, Copperline House<br>Harbour Tower, UK</span></div></div>
    <div class="contact-row" style="top:148px"><div class="ci"><svg width="12" height="18" viewBox="0 0 12 18"><rect x="1" y="1" width="10" height="16" rx="2" fill="none" stroke="#fff" stroke-width="2"/></svg></div><div><strong>PHONE:</strong><span>180 000 4417</span></div></div>
    <div class="contact-row" style="top:212px"><div class="ci"><svg width="16" height="12" viewBox="0 0 16 12"><rect width="16" height="12" fill="#fff"/><path d="M0 0l8 6 8-6" stroke="#1b1d22" fill="none"/></svg></div><div><strong>Mail:</strong><span>hello@copperlinecollective.com</span></div></div>
  </div>

  <div class="foot-col abs" style="left:812px;top:128px;width:290px;height:260px">
    <h5>CONTACT FORM</h5><div class="bar"></div>
    <div class="field" style="left:0;top:55px;width:138px;height:35px">Name</div>
    <div class="field" style="left:151px;top:55px;width:138px;height:35px">Phone</div>
    <div class="field" style="left:0;top:98px;width:289px;height:65px">Message</div>
    <div class="send" style="top:178px">SEND MESSAGE</div>
  </div>

  <div class="foot-rule"></div>
  <p class="copyright">Copyright © 2017 Copperline Collective. All Right Reserved</p>
  <a class="social" aria-label="chatterbook">chatterbook</a>
</footer>

</body>
</html>
```